Physical Medicine Clinic needs poster design

We need a poster design for a physical medicine clinic based in Dallas, Texas. We area multidisciplinary clinic focused on correcting the source of arthritic and postural dysfunctions with minimally invasive procedures. We want to communicate movement, health and trust.

Target Market(s)

Women 18 to 40

Industry/Entity Type

Healthcare

Font styles to use
Serif
Sans Serif

Requirements
Must have
• Our Logo for Vireo Medical Centers and the LUMEN Method Logo
• LUMEN stands for Balanced Mobility Therapy
Nice to have
• I will need this to be at the entry way of the office, at the front desk. This is to explain the vibe of our office. I sent the educational handouts primarily for the LUMEN logo and to give a little information about the office. This will also be used as a marketing tool as well

```html
<!DOCTYPE html>
<html lang="en">
<head>
<meta charset="utf-8">
<title>Vireo Medical Centers – Bulging Disc, Hip Pain and Shoulder Pain</title>
<link rel="stylesheet" href="https://fonts.googleapis.com/css2?family=Montserrat:ital,wght@0,500;0,700;0,800;1,700;1,800&family=Open+Sans:wght@400;600;700&family=Merriweather:ital,wght@1,700&display=swap">
<style>
  :root{
    --navy:#1d2f5c;
    --navy-dark:#14213f;
    --orange:#f08a24;
    --ink:#2b2f38;
    --grey:#e9ecf1;
    --grey-mid:#cfd5de;
    --bone:#e8c9a6;
    --spine:#c9a27e;
    --muscle:#c86a5a;
    --white:#ffffff;
  }
  *{box-sizing:border-box;margin:0;padding:0}
  html,body{width:849px;height:1200px;overflow:hidden;background:var(--white)}
  .poster{position:relative;width:849px;height:1200px;font-family:"Open Sans",Arial,sans-serif;color:var(--ink);overflow:hidden;background:var(--white)}
  .abs{position:absolute}
  .art{position:absolute;border-radius:4px}
  .brand{right:14px;top:12px;display:flex;align-items:center;gap:7px;font-family:"Open Sans",Arial,sans-serif;font-weight:700;font-size:13px;color:var(--navy)}
  .brand .dot{width:22px;height:22px;border-radius:50%;background:var(--orange)}
  .title{font-family:"Montserrat",Arial,sans-serif;font-weight:800;color:var(--navy);letter-spacing:.5px}
  .body-text{font-size:10.3px;line-height:1.45}
  .cause-head{font-family:"Merriweather",Georgia,serif;font-style:italic;font-weight:700;color:var(--navy);font-size:22px;text-align:center}
  .band-label{font-family:"Montserrat",Arial,sans-serif;font-style:italic;font-weight:800;color:var(--white)}
  .method{font-family:"Open Sans",Arial,sans-serif;font-weight:700;color:var(--navy);font-size:14px;display:flex;align-items:center;gap:6px}
  .method .sq{width:14px;height:14px;background:var(--orange)}
  .cause-list{list-style:none}
  .cause-list li{position:relative;padding-left:18px;font-size:10.1px;line-height:1.42;margin-bottom:8px}
  .cause-list li::before{content:"";position:absolute;left:0;top:3px;width:9px;height:9px;background:var(--orange)}
  .cause-list b{color:var(--navy)}
  .cause-list em{color:var(--orange);font-style:normal;font-weight:700}
  .posture{background:var(--orange);color:var(--white);border-radius:14px;font-family:"Montserrat",Arial,sans-serif;font-weight:700;font-size:13px;text-align:center;padding:6px 0}
  .shoulder-zone{left:0;top:760px;width:849px;height:440px;background:var(--grey)}
  .sub-head{font-family:"Montserrat",Arial,sans-serif;font-weight:800;color:var(--navy);font-size:13px}
  .accent{color:var(--orange);font-weight:700}
  .label{font-family:"Montserrat",Arial,sans-serif;font-weight:700;font-size:11px;color:var(--navy)}
</style>
</head>
<body>
<div class="poster">

  <!-- Header -->
  <div class="art" style="left:14px;top:10px;width:140px;height:172px;background:linear-gradient(160deg,var(--bone),var(--spine))" role="img" aria-label="Illustration of a spinal column with a bulging disc highlighted"></div>
  <div class="abs brand"><span class="dot"></span>Vireo Medical Centers</div>
  <h1 class="abs title" style="left:270px;top:14px;font-size:40px">BULGING DISC</h1>

  <p class="abs body-text" style="left:170px;top:70px;width:665px">When a disc degenerates, the soft inner gel of the disc can leak back into the spinal canal. This is known as disc herniation. The herniated disc material then puts pressure on the nerve, causing pain.</p>

  <h2 class="abs cause-head" style="left:170px;top:116px;width:665px">What is the Cause?</h2>
  <p class="abs body-text" style="left:170px;top:148px;width:665px">Disc herniation is most often the result of gradual disc degeneration. When injury occurs to soft tissue around your spine, your body will build up scar tissue to stabilize your spine. As a result, your spinal discs lose some of their water content, making them less flexible and more prone to tear or rupture, even from minor strain or twist.</p>

  <!-- How to Correct band -->
  <svg class="abs" style="left:0;top:208px" width="849" height="40" viewBox="0 0 849 40" aria-hidden="true">
    <rect x="0" y="0" width="849" height="40" fill="var(--grey)"/>
    <polygon points="0,0 400,0 370,40 0,40" fill="var(--navy)"/>
    <polygon points="400,0 418,0 388,40 370,40" fill="var(--orange)"/>
  </svg>
  <div class="abs band-label" style="left:60px;top:210px;font-size:27px">How to Correct</div>

  <div class="abs method" style="left:60px;top:268px"><span class="sq"></span>LUMEN Method</div>
  <p class="abs body-text" style="left:60px;top:292px;width:330px">The LUMEN Method allows the body to regain function, symmetry and muscular balance.</p>
  <div class="art" style="left:440px;top:254px;width:400px;height:92px;background:linear-gradient(90deg,#f1ddc8,var(--spine),#f1ddc8)" role="img" aria-label="Illustrations comparing a normal disc, a bulging disc and a herniated disc"></div>

  <!-- Hip pain -->
  <h2 class="abs title" style="left:18px;top:350px;font-size:38px">6 COMMON CAUSES OF HIP PAIN</h2>

  <div class="abs label" style="left:20px;top:402px;font-size:12px">OSTEOARTHRITIS</div>
  <div class="art" style="left:14px;top:420px;width:286px;height:270px;background:linear-gradient(170deg,var(--bone),var(--muscle))" role="img" aria-label="Hip joint illustrations showing osteoarthritis, muscle spasm, bursitis, tendinitis and a sprain or strain"></div>
  <p class="abs body-text" style="left:70px;top:530px;width:150px;font-size:8.5px;background:rgba(255,255,255,.85);padding:3px">The LUMEN Method allows the body to regain function, symmetry and muscular balance.</p>

  <ul class="abs cause-list" style="left:312px;top:404px;width:526px">
    <li><b>Arthritis:</b> The <em>most common</em> cause of chronic hip pain is <b>osteoarthritis</b>. This type of arthritis affects many people at any age – so never fear.</li>
    <li><b>Herniated disc and/or Sciatica:</b> Pinching of a nerve can cause pain in the back of the hip – the pain can start in your <b>lower back</b> and travel down to your buttocks and legs. This condition is called <b>Sciatica</b>.</li>
    <li><b>Tendinitis and Bursitis:</b> Many tendons around the hip connect the muscles to the hip joint. Bursa act as cushions between bones. These tendons and bursa can easily become <b>inflamed causing tendinitis and bursitis</b>.</li>
    <li><b>Muscle Spasm:</b> Muscular <b>imbalances</b> drawn from overworked muscles causing <b>Trigger Points</b>. Prolonged positions trip pain due to Trigger Points felt through the buttock muscles causing muscle spasm.</li>
    <li><b>Sprain/ Strain:</b> A hip sprain/strain is a condition that occurs due to stretching or tearing of <b>tight ligaments or muscles</b> that support the hip joint.</li>
    <li><b>Poor Posture:</b> Anterior Pelvic Tilt. A condition where a person’s pelvis tilts forward, pushing his or her torso forward bending the back in an exaggerated, extended posture of <b>sitting lacks pain hips</b> in this position.</li>
  </ul>
  <div class="abs posture" style="left:312px;top:664px;width:340px">All of these are caused by POOR POSTURE</div>

  <!-- Shoulder pain band -->
  <svg class="abs" style="left:0;top:712px" width="849" height="46" viewBox="0 0 849 46" aria-hidden="true">
    <rect x="0" y="0" width="849" height="46" fill="var(--navy)"/>
    <polygon points="0,0 150,0 125,46 0,46" fill="var(--navy-dark)"/>
    <polygon points="150,0 168,0 143,46 125,46" fill="var(--orange)"/>
    <polygon points="699,0 849,0 849,46 724,46" fill="var(--navy-dark)"/>
    <polygon points="681,0 699,0 724,46 706,46" fill="var(--orange)"/>
  </svg>
  <h2 class="abs band-label" style="left:0;top:717px;width:849px;text-align:center;font-size:30px;font-style:normal">SHOULDER PAIN</h2>

  <div class="abs shoulder-zone"></div>

  <div class="abs sub-head" style="left:20px;top:774px">2 Foot by 2 Foot Box</div>
  <p class="abs body-text" style="left:20px;top:792px;width:640px">Everything we do is in front of us. We reach forward when typing on keyboards, holding steering wheels and even while washing dishes. If you are a runner or a cyclist, you are likely to round your shoulders in your sport. If you lift weights to develop your “pecs”, you may build pectoral (chest) muscles that are so strong that they bring your shoulders forward.</p>
  <div class="art" style="left:680px;top:768px;width:160px;height:120px;background:linear-gradient(160deg,#d7dde6,var(--grey-mid))" role="img" aria-label="Figure working hunched inside a two foot by two foot box"></div>

  <div class="art" style="left:20px;top:856px;width:250px;height:300px;background:linear-gradient(170deg,var(--bone),var(--muscle))" role="img" aria-label="Anatomical illustration of the shoulder joint and surrounding muscles"></div>

  <p class="abs body-text" style="left:290px;top:858px;width:370px;text-align:center"><span class="accent">The shoulder joint has the most complex and unstable joints in the human body.</span> Muscle imbalances are the result of the chest and front shoulder muscles tightening up causing your shoulder stabilizers to overstretch, making them weaker.</p>

  <div class="art" style="left:290px;top:926px;width:170px;height:230px;background:linear-gradient(170deg,#d7dde6,var(--grey-mid))" role="img" aria-label="Posture illustration comparing rounded shoulders with aligned shoulders"></div>

  <div class="abs sub-head" style="left:480px;top:930px">Breaking Out of the BOX</div>
  <p class="abs body-text" style="left:480px;top:948px;width:355px">For the shoulder to function properly, you need to train <b>ALL the muscles</b> that help stabilize it.</p>

  <div class="abs method" style="left:480px;top:1000px;font-size:12px"><span class="sq" style="width:11px;height:11px"></span>LUMEN Method</div>
  <p class="abs body-text" style="left:480px;top:1020px;width:355px">The LUMEN Method trains all the involved muscle groups crucial for the long term health.</p>

</div>
</body>
</html>
```